Harborlane Products Flyer

Harborlane Lending Group, Inc.
Licensed Mortgage Company
Serving the DMV since 1997
"You open the Harborlane, we'll carry the load"
We specialize in...
FHA Loans
* Credit Scores as low as 500
* 203K Renovation Loans
Conventional Loans
* As little as 1% Down
* Bank Statement for Self-Employed
Investor Loans
* DSCR, & Fix & Flip
* Commercial & New Construction
Other Programs
* HELOCS & Reverse Mortgages
Call today for a free consultation
(800) 914-6027
www.harborlanehomeloans.com
NMLS #731860

```html
<!DOCTYPE html>
<html lang="en">
<head>
<meta charset="utf-8">
<title>Harborlane Products Flyer</title>
<link href="https://fonts.googleapis.com/css2?family=Tinos:wght@400;700&family=Poppins:wght@300;400&family=Open+Sans:wght@400;600;700&family=Oswald:wght@500&display=swap" rel="stylesheet">
<style>
  :root {
    --backdrop: #b0b0b0;
    --paper: #ffffff;
    --cream: #fdfaf3;
    --dot: #ededed;
    --blue: #2f5aa8;
    --blue-deep: #1f4088;
    --gold: #c8995a;
    --gold-light: #f2ddb3;
    --ink: #1b1b1b;
    --btn-ink: #2a2114;
  }
  * { margin: 0; padding: 0; box-sizing: border-box; }
  html, body { width: 879px; height: 1200px; overflow: hidden; background: var(--backdrop); }
  .flyer {
    position: absolute; left: 131px; top: 137px; width: 617px; height: 926px;
    background: var(--paper); overflow: hidden;
  }
  .flyer-art { position: absolute; inset: 0; }
  .brand {
    position: absolute; left: 100px; top: 40px; width: 166px; text-align: center;
    font-family: "Open Sans", sans-serif; color: var(--ink);
  }
  .brand-name {
    font-family: "Tinos", serif; font-weight: 700; color: var(--blue);
    font-size: 27px; line-height: 1; letter-spacing: 0.5px;
  }
  .brand-name-sub {
    font-family: "Tinos", serif; font-weight: 700; color: var(--blue);
    font-size: 15px; line-height: 1.2; letter-spacing: 0.5px; margin-top: 4px;
  }
  .brand-mark {
    display: block; width: 12px; height: 12px; border-radius: 50%;
    background: var(--gold); margin: 0 auto 8px;
  }
  .brand-tagline {
    font-size: 8.6px; font-weight: 600; letter-spacing: 0.6px; line-height: 1.15; margin-top: 14px;
  }
  .headline {
    position: absolute; left: 34px; top: 178px; width: 280px;
    font-family: "Tinos", serif; font-weight: 400; text-transform: uppercase;
  }
  .headline span { display: block; white-space: nowrap; }
  .headline .lead { color: var(--blue); font-size: 35px; line-height: 40px; letter-spacing: 0.5px; }
  .headline .accent { color: var(--gold); font-size: 38px; line-height: 46px; }
  .specialize-title {
    position: absolute; left: 0; width: 617px; top: 480px; text-align: center;
    font-family: "Tinos", serif; font-weight: 400; font-size: 52px; letter-spacing: 0.5px; text-transform: uppercase;
    background: linear-gradient(180deg, var(--blue) 30%, var(--blue-deep));
    -webkit-background-clip: text; background-clip: text; color: transparent;
  }
  .product { position: absolute; }
  .product-label {
    display: flex; align-items: center; justify-content: center;
    height: 38px; border-radius: 2px;
    background: linear-gradient(180deg, var(--gold-light), var(--gold));
    font-family: "Tinos", serif; font-size: 14.5px; letter-spacing: 0.6px;
    color: var(--btn-ink); text-transform: uppercase;
  }
  .product-points { list-style: none; margin-top: 14px; }
  .product-points li {
    position: relative; padding-left: 19px; height: 24.5px;
    font-family: "Poppins", sans-serif; font-size: 13.5px; color: var(--ink);
  }
  .product-points li::before {
    content: "*"; position: absolute; left: 2px; top: 1px;
    color: var(--gold); font-size: 15px;
  }
  .fha { left: 43px; top: 562px; }
  .fha .product-label { width: 148px; }
  .conventional { left: 323px; top: 562px; }
  .conventional .product-label { width: 196px; }
  .investor { left: 43px; top: 677px; }
  .investor .product-label { width: 148px; }
  .other { left: 323px; top: 677px; }
  .other .product-label { width: 196px; }
  .call-bar {
    position: absolute; left: 43px; top: 795px; width: 532px; height: 64px;
    border-radius: 3px; background: linear-gradient(180deg, #4f7fc2, var(--blue-deep));
    display: flex; align-items: center; justify-content: space-between; padding: 0 22px 0 19px;
    color: #ffffff;
  }
  .call-bar-text { font-family: "Tinos", serif; font-size: 13.5px; letter-spacing: 0.5px; text-transform: uppercase; }
  .call-bar-phone { font-family: "Oswald", sans-serif; font-weight: 500; font-size: 34px; letter-spacing: -0.5px; }
  .footer {
    position: absolute; left: 62px; right: 50px; top: 880px;
    display: flex; justify-content: space-between;
    font-family: "Open Sans", sans-serif; font-size: 16.5px; color: var(--ink);
  }
</style>
</head>
<body>
  <main class="flyer">
    <svg class="flyer-art" width="617" height="926" viewBox="0 0 617 926">
      <defs>
        <linearGradient id="ring-gold" x1="0" y1="0" x2="0" y2="1">
          <stop offset="0" stop-color="#f4e2bf"/>
          <stop offset="1" stop-color="#c4924f"/>
        </linearGradient>
        <linearGradient id="photo-tone" x1="0" y1="0" x2="0" y2="1">
          <stop offset="0" stop-color="#8a8578"/>
          <stop offset="0.45" stop-color="#d8d2c2"/>
          <stop offset="0.75" stop-color="#6f8f4a"/>
          <stop offset="1" stop-color="#4f8a2c"/>
        </linearGradient>
      </defs>
      <polygon class="cream-band" points="0,417 617,488 617,926 0,926" fill="var(--cream)"/>
      <circle class="dot" cx="341" cy="43" r="24" fill="var(--dot)"/>
      <circle class="dot" cx="48" cy="124" r="24" fill="var(--dot)"/>
      <circle class="dot" cx="144" cy="412" r="36" fill="var(--dot)"/>
      <circle class="dot" cx="358" cy="421" r="24" fill="var(--dot)"/>
      <circle class="dot" cx="279" cy="576" r="24" fill="var(--dot)"/>
      <circle class="dot" cx="593" cy="753" r="24" fill="var(--dot)"/>
      <circle class="hero-ring" cx="575" cy="236" r="236" fill="url(#ring-gold)"/>
      <circle class="hero-ring-cut" cx="592" cy="232" r="228" fill="var(--paper)"/>
      <circle class="hero-photo" cx="561" cy="236" r="201" fill="url(#photo-tone)" role="img" aria-label="Photo of a cheering family in front of their new house, the child holding a home for sale sign"/>
    </svg>

    <header class="brand">
      <span class="brand-mark"></span>
      <div class="brand-name">HARBORLANE</div>
      <div class="brand-name-sub">LENDING GROUP</div>
      <p class="brand-tagline">LICENSED MORTGAGE COMPANY<br>SERVING THE DMV SINCE 1997</p>
    </header>

    <h1 class="headline">
      <span class="lead">You open the</span>
      <span class="accent">Harborlane,</span>
      <span class="lead">we'll carry</span>
      <span class="accent">the load</span>
    </h1>

    <h2 class="specialize-title">We specialize in…</h2>

    <section class="product fha">
      <div class="product-label">FHA Loans</div>
      <ul class="product-points">
        <li>Credit Scores as low as 500</li>
        <li>203K Renovation Loans</li>
      </ul>
    </section>
    <section class="product conventional">
      <div class="product-label">Conventional Loans</div>
      <ul class="product-points">
        <li>As little as 1% Down</li>
        <li>Bank Statement for Self-Employed</li>
      </ul>
    </section>
    <section class="product investor">
      <div class="product-label">Investor Loans</div>
      <ul class="product-points">
        <li>DSCR, &amp; Fix &amp; Flip</li>
        <li>Commercial &amp; New Construction</li>
      </ul>
    </section>
    <section class="product other">
      <div class="product-label">Other Programs</div>
      <ul class="product-points">
        <li>HELOCS &amp; Reverse Mortgages</li>
      </ul>
    </section>

    <div class="call-bar">
      <span class="call-bar-text">Call today for a free consultation</span>
      <span class="call-bar-phone">(800) 914-6027</span>
    </div>

    <footer class="footer">
      <span class="footer-web">www.harborlanehomeloans.com</span>
      <span class="footer-license">NMLS #731860</span>
    </footer>
  </main>
</body>
</html>
```